Business Card Design For Marketing Agnecy LVP

Need business card design for marketing agency.

Doug Fenwick
President, CEO
1-555-302-4196
doug@boldpromoperksgroup.example
www.BoldPromoPerksGroup.example

Back Side:
Boost Sales Using Rewards, Incentives & Giveaways
Get A Free Sample Package

Target Market(s)

B2B

Industry/Entity Type

Marketing

Contact Information for Business Card

Doug Fenwick
President, CEO
1-555-302-4196

Back Side:
Get A Free Sample Package

Please note that my current url is OLD DESIGN. I am working on new design and want the business card to match color themes at least on new site. Here is the demo link for new site so you can see the colors I use, etc.

http://layoutcratehub.example/kq/doug/lvp_final/index.html

Requirements
Must have
• Please note that my current url is OLD DESIGN. I am working on new design and want the business card to match color themes at least on new site. Here is the demo link for new site so you can see the colors I use, etc.

Nice to have

Should not have

```html
<!DOCTYPE html>
<html lang="en">
<head>
<meta charset="utf-8">
<title>LVP Business Card</title>
<link rel="stylesheet" href="https://fonts.googleapis.com/css2?family=Jost:wght@400;500;600;700&display=swap">
<style>
  :root {
    --brand-blue: #1b75bc;
    --brand-green: #4caf50;
    --ink-grey: #4d4d4f;
    --paper: #ffffff;
    --backdrop: #ececec;
  }
  * { margin: 0; padding: 0; box-sizing: border-box; }
  html, body {
    width: 1005px; height: 1200px; overflow: hidden;
    background: var(--backdrop);
    font-family: "Jost", sans-serif;
  }
  .card {
    position: absolute;
    left: 82px;
    width: 840px; height: 478px;
    overflow: hidden;
    box-shadow: 0 10px 28px rgba(0,0,0,0.18);
  }
  .card--front { top: 80px; background: var(--paper); }
  .card--back { top: 642px; background: var(--brand-green); color: #fff; }

  /* front */
  .brand-name {
    position: absolute; left: 0; right: 0; top: 60px;
    text-align: center;
    font-size: 160px; font-weight: 700; line-height: 1;
    letter-spacing: -2px; color: var(--brand-blue);
  }
  .holder {
    position: absolute; right: 554px; top: 350px; text-align: right;
  }
  .holder__name {
    font-size: 20px; font-weight: 500; color: var(--brand-blue);
    letter-spacing: 0.2px;
  }
  .holder__title {
    font-size: 16px; font-weight: 500; color: var(--ink-grey); margin-top: 4px;
  }
  .divider {
    position: absolute; left: 311px; top: 295px;
    width: 1.5px; height: 143px;
    background: linear-gradient(to bottom, rgba(76,175,80,0), var(--brand-green) 30%, var(--brand-green) 70%, rgba(76,175,80,0));
  }
  .contacts {
    position: absolute; left: 337px; top: 342px; list-style: none;
  }
  .contacts li {
    display: flex; align-items: center;
    font-size: 16px; font-weight: 500; color: var(--ink-grey);
    height: 26.5px; letter-spacing: 0.3px;
  }
  .contacts svg { width: 14px; height: 14px; margin-right: 10px; flex: none; }
  .card-band {
    position: absolute; left: 0; bottom: 0; width: 840px; height: 12px;
  }

  /* back */
  .watermark {
    position: absolute; left: 0; right: 0; top: 90px; text-align: center;
    font-size: 230px; font-weight: 700; line-height: 1;
    color: rgba(255,255,255,0.06); letter-spacing: -4px;
  }
  .pitch {
    position: absolute; left: 0; right: 0; top: 224px; text-align: center;
  }
  .pitch__headline {
    display: inline-block; white-space: nowrap;
    font-size: 20px; font-weight: 700; letter-spacing: 0.2px;
    text-transform: uppercase; padding: 0 2px 6px;
    border-bottom: 1.5px solid #fff;
  }
  .pitch__offer {
    font-size: 19px; font-weight: 500; letter-spacing: 0.4px;
    text-transform: uppercase; margin-top: 8px;
  }
  .back-url {
    position: absolute; left: 0; right: 0; top: 412px; text-align: center;
    font-size: 16px; font-weight: 600; letter-spacing: 0.2px;
  }
</style>
</head>
<body>
  <section class="card card--front" aria-label="Business card front">
    <p class="brand-name">LVP</p>

    <div class="holder">
      <p class="holder__name">DOUG FENWICK</p>
      <p class="holder__title">President, CEO</p>
    </div>

    <div class="divider"></div>

    <ul class="contacts">
      <li>
        <svg viewBox="0 0 16 16" aria-hidden="true"><path fill="var(--brand-blue)" d="M3.6 1.2l2.2 2.6-1.3 1.6c.9 2 2.4 3.5 4.3 4.4l1.6-1.3 2.6 2.2-1.1 2.4C6.8 13 3 9.2 1.3 3.1z"/></svg>
        1-555-302-4196
      </li>
      <li>
        <svg viewBox="0 0 16 16" aria-hidden="true"><rect x="1" y="3" width="14" height="10" fill="var(--brand-blue)"/><path d="M1.5 3.5L8 9l6.5-5.5" fill="none" stroke="#fff" stroke-width="1.3"/></svg>
        doug@boldpromoperksgroup.example
      </li>
      <li>
        <svg viewBox="0 0 16 16" aria-hidden="true"><circle cx="8" cy="8" r="6.5" fill="none" stroke="var(--brand-blue)" stroke-width="1.5"/><ellipse cx="8" cy="8" rx="2.6" ry="6.5" fill="none" stroke="var(--brand-blue)" stroke-width="1.2"/><path d="M1.5 8h13" stroke="var(--brand-blue)" stroke-width="1.2"/></svg>
        www.BoldPromoPerksGroup.example
      </li>
    </ul>

    <svg class="card-band" viewBox="0 0 840 12" preserveAspectRatio="none" aria-hidden="true">
      <polygon points="0,0 421,0 416,12 0,12" fill="var(--brand-blue)"/>
      <polygon points="427,0 840,0 840,12 422,12" fill="var(--brand-green)"/>
    </svg>
  </section>

  <section class="card card--back" aria-label="Business card back">
    <div class="watermark" aria-hidden="true">LVP</div>
    <div class="pitch">
      <p class="pitch__headline">Boost Sales Using Rewards, Incentives &amp; Giveaways</p>
      <p class="pitch__offer">Get A Free Sample Package</p>
    </div>
    <p class="back-url">www.BoldPromoPerksGroup.example</p>
  </section>
</body>
</html>
```